I need a business card for my original fine art pieces

I would like a business card design including a logo design for a new business in the art world. I am based in the Hunter Valley NSW Australia. I am a contemporary figurative, encaustic and wildlife artist. I would like to be able to upload my email and mobile number to this as well. This design should be one that I can incorporate into banners and flyers etc. Id like to incorporate one of my own images or partial image into the background or somewhere below. My initials are RJ and I would like these used as a logo type. I would like the use of some colour and it to be bright and catchy. The final design should communicate artwork custom made and commissions available.

Overview: Original Fine Artworks for sale, online, art galleries etc, Custom made to order and by commission.

Target market is world wide audience and corporate world

My figurative work is painted using acrylics in a lot of natural ochre colours that reflect the Australian Outback, on canvas, linen, paper or board: My encaustic work is created in a contemporary abstract style using a blow torch and a made with a medium of 100% pure bees wax, Damar resin, mixed media and coloured pigments, applied to Birch board. My wildlife are created using coloured pencil and mixed media on a variety of paper types or board.

```html
<!DOCTYPE html>
<html lang="en">
<head>
<meta charset="utf-8">
<title>Rhea Jarvis – Business Card</title>
<link rel="stylesheet" href="https://fonts.googleapis.com/css2?family=Open+Sans:wght@400;700&family=Arimo:wght@400&display=swap">
<style>
  :root {
    --orange: #ff4a0a;
    --card-black: #000000;
    --ghost: #1c1c1c;
    --white: #ffffff;
    --bg-top: #bcbcbc;
    --bg-bottom: #ffffff;
  }
  html, body {
    margin: 0;
    padding: 0;
    width: 1200px;
    height: 900px;
    overflow: hidden;
  }
  .stage {
    position: relative;
    width: 1200px;
    height: 900px;
    background: linear-gradient(to bottom, var(--bg-top) 0%, #e4e4e4 55%, var(--bg-bottom) 100%);
    font-family: "Open Sans", sans-serif;
  }
  .card {
    position: absolute;
    top: 170px;
    width: 347px;
    height: 561px;
    background: var(--card-black);
    overflow: hidden;
  }
  .card--front { left: 259px; }
  .card--back { left: 631px; }

  .band { position: absolute; left: 0; width: 347px; }
  .band--top { top: 0; height: 60px; }
  .band--bottom { bottom: 0; height: 50px; }

  .front-name {
    position: absolute;
    left: 0; right: 0;
    top: 156px;
    margin: 0;
    text-align: center;
    font-size: 28px;
    font-weight: 700;
    line-height: 36px;
    letter-spacing: 0.04em;
    color: var(--orange);
  }

  .ring {
    position: absolute;
    box-sizing: border-box;
    border-radius: 50%;
  }
  .ring--brand {
    left: 117px; top: 198px;
    width: 112px; height: 112px;
    border: 3px solid var(--orange);
  }
  .ring--ghost { border: 4px solid var(--ghost); }
  .ring--ghost-top {
    left: 155px; top: -125px;
    width: 390px; height: 390px;
  }
  .ring--ghost-bottom {
    left: -120px; top: 302px;
    width: 356px; height: 356px;
  }

  .contact {
    position: absolute;
    left: 0; right: 0;
    top: 330px;
    text-align: center;
    color: var(--white);
  }
  .contact__name {
    margin: 0;
    font-size: 19px;
    font-weight: 700;
    color: var(--orange);
    line-height: 1.1;
  }
  .contact__role {
    margin: 2px 0 0;
    font-size: 14px;
    line-height: 1.3;
  }
  .contact__list {
    list-style: none;
    margin: 15px 0 0;
    padding: 0;
    font-size: 14px;
    line-height: 21px;
  }
  .contact__label { color: var(--orange); font-weight: 700; }
  .contact__address {
    margin: 11px 0 0;
    font-style: normal;
    font-size: 14px;
    line-height: 17px;
  }

  .brand {
    position: absolute;
    left: 0; right: 0;
    top: 311px;
    text-align: center;
  }
  .brand__name {
    margin: 0;
    font-family: "Open Sans", sans-serif;
    font-weight: 700;
    font-size: 31px;
    color: var(--orange);
    letter-spacing: 0.03em;
    line-height: 1.1;
  }
  .brand__tagline {
    margin: 3px 0 0;
    font-family: "Arimo", sans-serif;
    font-size: 14.5px;
    letter-spacing: 0.2em;
    color: var(--white);
    padding-left: 0.2em;
  }
</style>
</head>
<body>
<main class="stage">

  <section class="card card--front" aria-label="Business card front">
    <svg class="band band--top" viewBox="0 0 347 60" aria-hidden="true">
      <path d="M101 0 H246 V47 Q173.5 22 101 47 Z" fill="var(--orange)"/>
    </svg>

    <p class="front-name">RHEA JARVIS</p>

    <div class="contact">
      <p class="contact__name">DANIEL HART</p>
      <p class="contact__role">Managing Director</p>
      <ul class="contact__list">
        <li><span class="contact__label">P:</span> 555-014-2368</li>
        <li><span class="contact__label">E:</span> hello@rheajarvis.art</li>
        <li><span class="contact__label">W:</span> www.rheajarvis.art</li>
      </ul>
      <address class="contact__address">88 Vineyard Road, Pokolbin<br>NSW, 2320</address>
    </div>

    <svg class="band band--bottom" viewBox="0 0 347 50" aria-hidden="true">
      <path d="M101 9 Q173.5 32 246 9 V50 H101 Z" fill="var(--orange)"/>
    </svg>
  </section>

  <section class="card card--back" aria-label="Business card back">
    <div class="ring ring--ghost ring--ghost-top" aria-hidden="true"></div>
    <div class="ring ring--ghost ring--ghost-bottom" aria-hidden="true"></div>

    <div class="ring ring--brand" aria-hidden="true"></div>

    <div class="brand">
      <h1 class="brand__name">Rhea Jarvis</h1>
      <p class="brand__tagline">ORIGINAL FINE ARTWORKS</p>
    </div>
  </section>

</main>
</body>
</html>
```